Refresh of far from plain IT company website

Our web site is starting to show it's age. You can see the existing site here: www.plumbwick.net. As a growing company we want to come across as a dynamic collection of IT experts.

We want to update the design so are open to any colour palette and look, but want to retain our current table logo. We use the logo on our business cards but with a white background - see the attached file, so you don't need to keep the brown or the green.

The design should consider the range of browsers that will be looking at the site - so please show how it will look on a wide screen laptop and a 768x1024 tablet.

We want to add some pages about our team and their skills, probably with photos of each person on the team.

This is an uncoded project - the PSD files of the design is required, not coding.
Updates

Thanks everyone for the submissions so far.  It's a holiday day in the UK today but we will get some feedback on the designs so far out to you.

Target Market(s)

Architects and other creative types looking for IT support

Industry/Entity Type

Business

Font styles to use
Serif
Sans Serif

Requirements
Must have
• Must look good on a laptop and an iPad.

```html
<!DOCTYPE html>
<html lang="en">
<head>
<meta charset="utf-8">
<title>plumbwick – Serious IT support for business</title>
<link href="https://fonts.googleapis.com/css2?family=Ubuntu:ital,wght@0,400;0,500;0,700;1,400;1,700&family=Open+Sans:wght@400;600&display=swap" rel="stylesheet">
<style>
:root{
  --plum:#8e0a4f;
  --gold:#d8ab13;
  --ink:#333;
  --muted:#666;
  --line:#dcdcdc;
  --panel:#efefef;
  --footer:#333;
  --icon:#555;
}
*{box-sizing:border-box;margin:0;padding:0}
html,body{width:1034px;height:1200px;overflow:hidden;background:#fff}
body{position:relative;font-family:"Open Sans",Arial,sans-serif;color:var(--ink)}
.abs{position:absolute}
.top-bar{left:0;top:0;width:1034px;height:3px;background:var(--plum)}
.brand{left:198px;top:28px;display:flex;align-items:center;gap:12px}
.brand-mark{width:46px;height:34px;background:var(--gold)}
.brand-name{font-family:"Ubuntu",sans-serif;font-weight:500;font-size:42px;color:var(--plum);line-height:1}
.call{right:191px;top:18px;font-family:"Ubuntu",sans-serif;font-size:14px;color:#444;letter-spacing:.3px}
.social{right:191px;top:54px;display:flex;gap:6px}
.social span{width:27px;height:27px;border-radius:50%;background:#e6e6e6;box-shadow:0 1px 2px rgba(0,0,0,.3)}
.nav{left:196px;top:96px;display:flex;font-family:"Ubuntu",sans-serif;font-size:10px;text-transform:uppercase;color:#444}
.nav a{color:inherit;text-decoration:none;padding:3px 18px 0;height:26px;border-left:1px solid #bbb;line-height:12px}
.nav a:first-child{border-left:0;padding-left:4px;color:var(--plum);font-weight:500;border-bottom:3px solid var(--plum)}
.nav-rule{left:0;top:122px;width:1034px;height:1px;background:#e4e4e4}
.hero{left:0;top:123px;width:1034px;height:331px;background:linear-gradient(100deg,#f4f4f4 0%,#ececec 25%,#e9c8b8 42%,#dfe6ee 62%,#9fbbdd 80%,#b7cbe6 100%)}
.slogan{left:206px;top:358px;font-family:"Ubuntu",sans-serif;font-style:italic;font-size:32px;color:#333}
.dots{left:777px;top:385px;display:flex;gap:8px}
.dots span{width:11px;height:11px;border-radius:50%;border:1.5px solid #fff;background:rgba(255,255,255,.3)}
.dots span:first-child{background:var(--plum)}
.service-rule{left:0;top:452px;width:1034px;height:4px;background:var(--plum)}
.service-band{left:0;top:456px;width:1034px;height:52px;background:linear-gradient(#eee,#fff)}
.service{width:140px;text-align:center;top:426px;font-family:"Ubuntu",sans-serif;font-weight:500;font-size:11px;color:#333}
.service .disc{width:52px;height:52px;border-radius:50%;margin:0 auto 12px;background:#5b5b5b;border:3px solid #fff;box-shadow:0 1px 3px rgba(0,0,0,.4);display:flex;align-items:center;justify-content:center}
.service.active .disc{background:var(--plum);box-shadow:0 2px 0 var(--gold)}
h2{font-family:"Ubuntu",sans-serif;font-style:italic;font-weight:700;font-size:17px;color:var(--plum);padding-bottom:5px;border-bottom:1px solid var(--line)}
.about{left:198px;top:532px;width:414px}
.about p{font-size:10.5px;line-height:18px;margin-top:10px;color:#333}
.about p+p{margin-top:13px}
.read-more{position:absolute;right:0;top:176px;font-size:10.5px;color:var(--gold);font-family:"Ubuntu",sans-serif}
.team{left:642px;top:528px;width:192px;height:192px;border-radius:50%;border:3px solid var(--plum);overflow:hidden;background:linear-gradient(#f4f6f9,#c9d6e6);box-shadow:0 8px 10px -6px rgba(0,0,0,.3)}
.team-band{position:absolute;left:0;bottom:0;width:100%;height:60px;background:var(--plum);color:#fff;text-align:center;font-family:"Ubuntu",sans-serif;font-weight:500;font-size:21px;padding-top:10px}
.col{top:756px;width:310px}
.box{margin-top:10px;height:226px;border:1px solid #ccc;border-radius:3px;background:var(--panel);box-shadow:inset 0 0 0 3px #fff,0 8px 8px -6px rgba(0,0,0,.35);padding:0 14px}
.quote{display:flex;height:110px;padding-top:12px;border-bottom:1px solid #e0e0e0}
.quote:last-child{border-bottom:0}
.person{width:82px;text-align:center;font-family:"Ubuntu",sans-serif}
.avatar{width:62px;height:62px;border-radius:50%;background:linear-gradient(#d9d9d9,#9a9a9a);border:3px solid #fff;margin:0 auto 4px;box-shadow:0 1px 2px rgba(0,0,0,.3)}
.person b{display:block;font-weight:500;font-size:12px;color:#333}
.person small{font-size:9px;color:#666}
.quote p{flex:1;margin-left:16px;border-left:1px solid #ddd;padding:6px 0 0 28px;font-size:9.3px;line-height:13.5px;position:relative}
.quote p:before{content:"\201C";position:absolute;left:8px;top:-2px;font-size:26px;color:#999;font-family:Georgia,serif}
.news{display:flex;gap:14px;height:75px;padding:14px 8px 0;border-bottom:1px solid #e0e0e0}
.news:last-child{border-bottom:0}
.news strong{display:block;font-family:"Ubuntu",sans-serif;font-weight:500;font-size:10px;color:var(--plum);margin-bottom:4px}
.news p{font-size:9.8px;line-height:14px}
.pager{display:flex;justify-content:center;gap:7px;margin-top:8px}
.pager svg{width:14px;height:14px}
.footer{left:0;top:1058px;width:1034px;height:120px;background:var(--footer);color:#fff}
.footer h3{font-family:"Ubuntu",sans-serif;font-weight:400;font-size:13px;margin-bottom:12px}
.links{left:198px;top:18px;width:190px;border-right:1px solid #555;height:90px}
.links ul{list-style:none;float:left;width:85px;font-size:8.5px;line-height:18px;text-transform:uppercase}
.links li:before{content:"›";color:var(--gold);margin-right:8px}
.signup{left:430px;top:18px;width:164px;font-size:9.5px;line-height:11px}
.signup input{display:block;margin:8px 0 6px -2px;width:114px;height:17px;border:0;border-radius:2px;font-size:8px;padding:0 5px;font-family:inherit}
.signup button{background:var(--plum);color:#fff;border:1px solid #fff;font:700 9px "Open Sans",sans-serif;padding:2px 7px;border-radius:2px}
.signup-rule{left:593px;top:43px;width:1px;height:66px;background:#555}
.contact{left:635px;top:18px;width:210px}
.map{position:absolute;left:0;top:24px;width:81px;height:63px;background:linear-gradient(135deg,#e8e6df,#d4d9cf)}
.contact ul{position:absolute;left:94px;top:24px;list-style:none;font-size:9px;line-height:11px;width:120px}
.contact li{display:flex;gap:8px;margin-bottom:5px}
.contact li svg{flex:none;width:10px;height:10px}
.copy{left:0;top:1178px;width:1034px;height:22px;background:var(--plum);color:#fff;text-align:center;font-family:"Ubuntu",sans-serif;font-size:10.5px;line-height:22px}
</style>
</head>
<body>
<div class="abs top-bar"></div>

<header>
  <div class="abs brand"><span class="brand-mark"></span><span class="brand-name">plumbwick</span></div>
  <div class="abs call">CALL US: 020 7946 0182</div>
  <div class="abs social" aria-label="Social links"><span></span><span></span><span></span><span></span></div>
  <nav class="abs nav">
    <a href="#">Home</a><a href="#">About Us</a><a href="#">What We Do</a><a href="#">News Blog</a><a href="#">Articles</a><a href="#">Clients</a><a href="#">Partners</a><a href="#">Contact Us</a>
  </nav>
  <div class="abs nav-rule"></div>
</header>

<section>
  <div class="abs hero" role="img" aria-label="Photo of a hand drawing a cloud with the words cloud computing"></div>
  <div class="abs slogan">Serious IT support for business</div>
  <div class="abs dots"><span></span><span></span><span></span><span></span></div>
</section>

<section>
  <div class="abs service-band"></div>
  <div class="abs service-rule"></div>
  <div class="abs service" style="left:188px"><div class="disc"><svg width="26" height="26" viewBox="0 0 24 24"><path d="M15 3a5 5 0 0 0-4.6 6.9L3 17.3 6.7 21l7.4-7.4A5 5 0 0 0 21 9l-3 3-3-3 3-3a5 5 0 0 0-3-3z" fill="#fff"/></svg></div>It Support &amp; Management</div>
  <div class="abs service" style="left:320px"><div class="disc"><svg width="30" height="22" viewBox="0 0 30 22"><path d="M7 19h16a5 5 0 0 0 0-10 8 8 0 0 0-15-1 5.5 5.5 0 0 0-1 11z" fill="none" stroke="#fff" stroke-width="2.5"/></svg></div>Cloud Computing</div>
  <div class="abs service active" style="left:449px"><div class="disc"><svg width="22" height="30" viewBox="0 0 22 30"><path d="M11 1c2 4 6 5 6 10a6 6 0 0 1-12 0c0-3 2-4 3-7 1 2 2 3 3 3z" fill="#fff"/><rect x="6" y="16" width="10" height="13" rx="1" fill="#fff" stroke="#8e0a4f"/></svg></div>Disaster Recovery</div>
  <div class="abs service" style="left:580px"><div class="disc"><svg width="20" height="28" viewBox="0 0 20 28"><rect x="5" y="1" width="10" height="18" fill="#fff"/><path d="M10 19v5M2 26h16" stroke="#fff" stroke-width="2"/></svg></div>Virtualisation</div>
  <div class="abs service" style="left:704px"><div class="disc"><svg width="28" height="26" viewBox="0 0 28 26"><path d="M14 2 3 24M14 2l11 22M7 16h14" stroke="#fff" stroke-width="3" fill="none"/></svg></div>CAD Services</div>
</section>

<section class="abs about">
  <h2>ABOUT US</h2>
  <p>Lorem ipsum dolor sit amet, consectetuer adipiscing elit, sed diam nonummy nibh euismod tincidunt ut laoreet dolore magna aliquam erat volutpat. Ut wisi enim ad minim veniam, quis nostrud exerci tation ullamcorper suscipit lobortis nisl ut aliquip ex ea comsed diam nonummy nibh euism od tincidunt ut laoreet dolore magna aliquam erat volutpat.</p>
  <p>Lorem ipsum dolor sit amet, consectetuer adipiscing elit, sed diam nonummy nibh euismod tincidunt ut laoreet dolore magna aliquam erat volutpat. Ut wisi enim ad minim veniam, quis nostrud....</p>
  <a class="read-more">READ MORE...</a>
</section>

<div class="abs team" role="img" aria-label="Group photo of the team">
  <div class="team-band">OUR TEAM</div>
</div>

<section class="abs col" style="left:198px">
  <h2>TESTIMONIALS</h2>
  <div class="box">
    <div class="quote"><div class="person"><div class="avatar" role="img" aria-label="Client portrait"></div><b>Daniel Hartley</b><small>Businessman</small></div>
      <p>Lorem ipsum dolor sit amet, consectetuer adipiscing elit, sed diam nonummy nibh euismod tincidunt ut laoreet dolore magna aliquam erat volutpat. Ut wisi enim ad minim. ”</p></div>
    <div class="quote"><div class="person"><div class="avatar" role="img" aria-label="Client portrait"></div><b>Daniel Hartley</b><small>Businessman</small></div>
      <p>Lorem ipsum dolor sit amet, consectetuer adipiscing elit, sed diam nonummy nibh euismod tincidunt ut laoreet dolore magna aliquam erat volutpat. Ut wisi enim ad minim. ”</p></div>
  </div>
  <div class="pager"><svg viewBox="0 0 14 14"><circle cx="7" cy="7" r="6" fill="none" stroke="#555"/><path d="M10 7H4m2.5-2.5L4 7l2.5 2.5" stroke="#555" fill="none"/></svg><svg viewBox="0 0 14 14"><circle cx="7" cy="7" r="6" fill="none" stroke="#555"/><path d="M4 7h6M7.5 4.5 10 7 7.5 9.5" stroke="#555" fill="none"/></svg></div>
</section>

<section class="abs col" style="left:534px">
  <h2>LATEST NEWS</h2>
  <div class="box">
    <div class="news"><svg width="30" height="30" viewBox="0 0 30 30"><rect x="2" y="5" width="26" height="23" rx="3" fill="none" stroke="#666" stroke-width="2.5"/><path d="M2 11h26M9 2v6M21 2v6M8 16h3M14 16h3M20 16h3M8 22h3M14 22h3M20 22h3" stroke="#666" stroke-width="2.5"/></svg><div><strong>12-APR-2014</strong><p>Lorem ipsum dolor sit amet, consectetuer adipiscil ng elit, sed diam nonummy nibh...</p></div></div>
    <div class="news"><svg width="30" height="30" viewBox="0 0 30 30"><rect x="2" y="5" width="26" height="23" rx="3" fill="none" stroke="#666" stroke-width="2.5"/><path d="M2 11h26M9 2v6M21 2v6M8 16h3M14 16h3M20 16h3M8 22h3M14 22h3M20 22h3" stroke="#666" stroke-width="2.5"/></svg><div><strong>15-APR-2014</strong><p>Lorem ipsum dolor sit amet, consectetuer adipiscil ng elit, sed diam nonummy nibh...</p></div></div>
    <div class="news"><svg width="30" height="30" viewBox="0 0 30 30"><rect x="2" y="5" width="26" height="23" rx="3" fill="none" stroke="#666" stroke-width="2.5"/><path d="M2 11h26M9 2v6M21 2v6M8 16h3M14 16h3M20 16h3M8 22h3M14 22h3M20 22h3" stroke="#666" stroke-width="2.5"/></svg><div><strong>17-APR-2014</strong><p>Lorem ipsum dolor sit amet, consectetuer adipiscil ng elit, sed diam nonummy nibh...</p></div></div>
  </div>
  <div class="pager"><svg viewBox="0 0 14 14"><circle cx="7" cy="7" r="6" fill="none" stroke="#555"/><path d="M10 7H4m2.5-2.5L4 7l2.5 2.5" stroke="#555" fill="none"/></svg><svg viewBox="0 0 14 14"><circle cx="7" cy="7" r="6" fill="none" stroke="#555"/><path d="M4 7h6M7.5 4.5 10 7 7.5 9.5" stroke="#555" fill="none"/></svg></div>
</section>

<footer class="abs footer">
  <div class="abs links"><h3>Quick Links</h3>
    <ul><li>Home</li><li>About Us</li><li>What We Do</li><li>News Blog</li></ul>
    <ul><li>Articles</li><li>Clients</li><li>Partners</li><li>Contact Us</li></ul>
  </div>
  <div class="abs signup"><h3 style="margin-bottom:8px">Newsletter Signup</h3>
    Lorem ipsum dolor sit amet, consectetuer adipiscing elit.
    <input type="text" placeholder="Enter your email address">
    <button>SUBMIT</button>
  </div>
  <div class="abs signup-rule"></div>
  <div class="abs contact"><h3>Contact Info</h3>
    <div class="map" role="img" aria-label="Street map showing the office location"></div>
    <ul>
      <li><svg viewBox="0 0 10 10"><path d="M5 10 1.5 4.5a3.5 3.5 0 1 1 7 0z" fill="#d8ab13"/><circle cx="5" cy="3.8" r="1.3" fill="#333"/></svg><span>Lorem ipsum dolor sit amet, consectetuer adipiscing elit.</span></li>
      <li><svg viewBox="0 0 10 10"><circle cx="5" cy="5" r="4.3" fill="none" stroke="#d8ab13"/><path d="M3.5 3c0 2 1.5 3.8 3.3 4" stroke="#d8ab13" fill="none"/></svg><span>020 7946 0182</span></li>
      <li><svg viewBox="0 0 10 10"><rect x=".5" y="2" width="9" height="6.5" fill="#d8ab13"/><path d="M.5 2 5 5.5 9.5 2" stroke="#333" fill="none"/></svg><span>website@plumbwick.net</span></li>
    </ul>
  </div>
</footer>
<div class="abs copy">© 2014 plumbwick. All Rights Reserved.</div>
</body>
</html>
```